Emerging Australian photographer

I'm based in Cunderdin, a small rural town in the Wheatbelt area of Western Australia. So its a good thing that I love to travel further afield both for pleasure and for work. To me that is one and the same thing in any event!

My desire is to take photos that make the viewers heart skip. I love taking photos of people doing the things they love or being with the people they love. For me, the joy of photography comes with capturing the 'moments between the moments'. I like candid photography best of all - like when the new husband is staring joyfully at his bride and at that minute is unaware of the photographer capturing the moment.

I am available for weddings, engagements, birthdays, special events, newborns, family or individual portraits. By the end of the year I will be accredited with the Southern Guild of Accredited Image Makers.

I need a card that stands out but is elegant and would sit well on the table at a wedding or be given out in the church grounds. Classy and a little bit sassy.

Target Market(s)

Consumers who are seeking photographic services, eg wedding guests who see me at work and make enquiries.

Industry/Entity Type

Church

Contact Information for Business Card

Tamsin Everly Photography
Tamsin Everly
0452 306 718
www.tamsineverly-studio.com.au
photos@tamsineverly-studio.com.au

Requirements
Must have
• Must fit with the theme in the watermarks, but be crisp and modern.
Nice to have
• However it's not essential to have the pink! Chatterly and Pipsqueak logos.
Should not have
• Old style fonts like times new roman.

```html
<!DOCTYPE html>
<html lang="en">
<head>
<meta charset="utf-8">
<title>Tamsin Everly Photography – Business Card</title>
<link rel="stylesheet" href="https://fonts.googleapis.com/css2?family=Arimo:wght@400;700&family=Dancing+Script:wght@500&display=swap">
<style>
  :root {
    --backdrop: #e8e6e3;
    --card: #f9f9f8;
    --ink: #5a5a5c;
    --ink-soft: #8a8a8c;
    --blush: #ee8fb4;
    --card-shadow: rgba(40, 35, 30, 0.18);
  }
  * { margin: 0; padding: 0; box-sizing: border-box; }
  html, body {
    width: 916px;
    height: 1200px;
    overflow: hidden;
    background: var(--backdrop);
  }
  .canvas {
    position: relative;
    width: 916px;
    height: 1200px;
  }
  .card {
    position: absolute;
    left: 78px;
    width: 760px;
    height: 440px;
    background: var(--card);
    border-radius: 26px;
    box-shadow: 0 10px 28px var(--card-shadow);
    overflow: hidden;
  }
  .card--front { top: 120px; }
  .card--back { top: 640px; }

  /* Front */
  .brand {
    position: absolute;
    display: flex;
    align-items: center;
    gap: 14px;
    font-family: "Dancing Script", cursive;
    font-weight: 500;
    color: var(--ink);
    white-space: nowrap;
  }
  .brand__dot {
    width: 14px;
    height: 14px;
    border-radius: 50%;
    background: var(--blush);
    flex: none;
  }
  .card--front .brand {
    left: 0;
    right: 0;
    top: 150px;
    justify-content: center;
    font-size: 58px;
  }
  .website {
    position: absolute;
    left: 0;
    right: 0;
    top: 278px;
    text-align: center;
    font-family: "Arimo", sans-serif;
    font-size: 17px;
    letter-spacing: 0.42em;
    color: var(--ink);
  }
  .website__domain { color: var(--blush); }

  /* Back */
  .card--back .brand {
    left: 0;
    right: 0;
    top: 56px;
    justify-content: center;
    font-size: 36px;
  }
  .details {
    position: absolute;
    right: 60px;
    bottom: 56px;
    text-align: right;
    font-family: "Arimo", sans-serif;
    color: var(--ink);
  }
  .details__name {
    font-size: 30px;
    font-weight: 400;
    line-height: 1;
  }
  .details__first { color: var(--blush); }
  .details__role {
    margin-top: 4px;
    font-size: 17px;
    letter-spacing: 0.38em;
    color: var(--blush);
  }
  .details__contact {
    margin-top: 14px;
    font-size: 16px;
    line-height: 1.45;
  }
  .details__label { color: var(--blush); margin-right: 4px; }
</style>
</head>
<body>
<main class="canvas">

  <section class="card card--front" aria-label="Business card front">
    <div class="brand">
      <span class="brand__dot"></span>
      <span class="brand__name">tamsin everly photography</span>
    </div>
    <p class="website">www.<span class="website__domain">tamsineverly-studio</span>.com.au</p>
  </section>

  <section class="card card--back" aria-label="Business card back">
    <div class="brand">
      <span class="brand__dot"></span>
      <span class="brand__name">tamsin everly photography</span>
    </div>
    <div class="details">
      <h1 class="details__name"><span class="details__first">Tamsin</span> Everly</h1>
      <p class="details__role">Photographer</p>
      <p class="details__contact">
        <span class="details__label">Phone</span>0452 306 718<br>
        <span class="details__label">Email</span>photos@tamsineverly-studio.com.au
      </p>
    </div>
  </section>

</main>
</body>
</html>
```